IT Company requires new Business Card design.

Over the years we have had a few different business card designs. We are now due for new cards across the board for all staff. We felt this would be a good time to start fresh with a new design. Our traditional card simply had our details on the front, and a list of services on the back. We don't particularly need the list of services, we have had cards where the only thing on the rear of the card was our logo.
Feel free to be creative, we would like our tag line "Complete IT Management" to appear at some point, doesn't necessarily have to be with the logo.
I have attached samples and drafts of various previous cards we have used over the years.

```html
<!DOCTYPE html>
<html lang="en">
<head>
<meta charset="utf-8">
<title>Ridgeway IT – Business Card</title>
<link rel="stylesheet" href="https://fonts.googleapis.com/css2?family=Open+Sans:wght@300;400;700&display=swap">
<style>
  :root {
    --slate: #5f6f7e;
    --slate-soft: #7a8692;
    --ink: #3a3f45;
    --paper: #ffffff;
    --band: #1e1f21;
    --band-edge: #5b5f66;
    --band-text: #f2f2f2;
  }
  * { box-sizing: border-box; margin: 0; padding: 0; }
  html, body {
    width: 1200px;
    height: 669px;
    overflow: hidden;
    background: var(--paper);
  }
  .card {
    position: relative;
    width: 1200px;
    height: 669px;
    background: var(--paper);
    font-family: "Open Sans", Arial, sans-serif;
    overflow: hidden;
  }
  .card__band {
    position: absolute;
    inset: 0;
    width: 1200px;
    height: 669px;
  }
  .brand {
    position: absolute;
    top: 96px;
    right: 34px;
    display: flex;
    align-items: center;
    gap: 24px;
  }
  .brand__square {
    width: 118px;
    height: 118px;
    background: var(--slate);
  }
  .brand__text {
    display: flex;
    flex-direction: column;
    align-items: flex-start;
  }
  .brand__name {
    color: var(--slate);
    font-weight: 700;
    font-size: 46px;
    line-height: 52px;
    letter-spacing: 0.5px;
  }
  .brand__tagline {
    margin-top: 8px;
    color: var(--slate);
    font-weight: 400;
    font-size: 14px;
    letter-spacing: 2.6px;
    text-transform: uppercase;
  }
  .person {
    position: absolute;
    left: 30px;
    top: 214px;
  }
  .person__name {
    color: var(--slate);
    font-weight: 700;
    font-size: 39px;
    line-height: 46px;
    letter-spacing: 0.3px;
  }
  .person__role {
    color: var(--slate-soft);
    font-weight: 300;
    font-size: 31px;
    line-height: 40px;
  }
  .contacts {
    position: absolute;
    left: 30px;
    top: 376px;
    list-style: none;
  }
  .contacts__item {
    display: flex;
    align-items: center;
    height: 40.5px;
    color: var(--ink);
    font-weight: 300;
    font-size: 27px;
  }
  .contacts__icon {
    width: 26px;
    height: 26px;
    margin-right: 22px;
    fill: var(--slate);
    flex: none;
  }
  .address {
    position: absolute;
    right: 34px;
    top: 565px;
    text-align: right;
    color: var(--band-text);
    font-weight: 300;
    font-size: 27px;
    line-height: 38px;
  }
</style>
</head>
<body>
<div class="card">
  <svg class="card__band" viewBox="0 0 1200 669" aria-hidden="true">
    <polygon points="0,620 1200,432 1200,669 0,669" fill="var(--band-edge)"/>
    <polygon points="0,626 1200,438 1200,669 0,669" fill="var(--band)"/>
  </svg>

  <div class="brand">
    <div class="brand__square" aria-hidden="true"></div>
    <div class="brand__text">
      <div class="brand__name">RIDGEWAY IT</div>
      <div class="brand__tagline">Managed tech for business</div>
    </div>
  </div>

  <div class="person">
    <div class="person__name">DANIEL HART</div>
    <div class="person__role">Position</div>
  </div>

  <ul class="contacts">
    <li class="contacts__item">
      <svg class="contacts__icon" viewBox="0 0 24 24" aria-label="Phone"><path d="M6.6 10.8c1.4 2.8 3.8 5.1 6.6 6.6l2.2-2.2c.3-.3.7-.4 1-.2 1.1.4 2.3.6 3.6.6.6 0 1 .4 1 1V20c0 .6-.4 1-1 1C10.6 21 3 13.4 3 4c0-.6.4-1 1-1h3.5c.6 0 1 .4 1 1 0 1.3.2 2.5.6 3.6.1.3 0 .7-.2 1L6.6 10.8z"/></svg>
      08 5550 1430
    </li>
    <li class="contacts__item">
      <svg class="contacts__icon" viewBox="0 0 24 24" aria-label="Mobile"><path d="M8 1h8a2 2 0 0 1 2 2v18a2 2 0 0 1-2 2H8a2 2 0 0 1-2-2V3a2 2 0 0 1 2-2zm0 2.2v15.6h8V3.2H8zm4 16.6a1 1 0 1 0 0 2 1 1 0 0 0 0-2z"/></svg>
      0400 555 718
    </li>
    <li class="contacts__item">
      <svg class="contacts__icon" viewBox="0 0 24 24" aria-label="Fax"><path d="M7 3h10v4H7V3zM4 8h16a2 2 0 0 1 2 2v6h-4v5H6v-5H2v-6a2 2 0 0 1 2-2zm4 7v4h8v-4H8zm10-5a1 1 0 1 0 0 2 1 1 0 0 0 0-2z"/></svg>
      08 5550 1432
    </li>
    <li class="contacts__item">
      <svg class="contacts__icon" viewBox="0 0 24 24" aria-label="Email"><path d="M12 2 2 9v12h20V9L12 2zm0 2.4 7.6 5.3L12 14.5 4.4 9.7 12 4.4zM4 11.9l8 5 8-5V19H4v-7.1z"/></svg>
      daniel@ridgewayit.com.au
    </li>
  </ul>

  <div class="address">
    7 / 22 Corella Drive, Bibra Park, 6163<br>
    www.ridgewayit.com.au
  </div>
</div>
</body>
</html>
```